Candle Box & Belly Band Design

Design Candle Box for Soy Candles along with a belly band design that can be used on off the shelf coloured boxes. It is for a premium brand of candle - so i want the packaging to reflect this. I have included must haves below.

The candle boxes will be a few different sizes, but for the purpose of the design it would be something like a cube 12 x 12 x 12 cms

The belly band for standard boxes to be something like 5cm wide on a 12 x 12 x 12cms cube box that goes all the way around the top to the bottom - holding the lid on and providing all the relevant information. Example of box with belly band uploaded

Our company Name : Clover & Jude - our logo is uploaded

Target Market(s)

Premium Candle Buyers

Colors

Designer to choose colors to be used in the design.

Requirements
Must have
• Must have our logo - our logo can be in any colour
• Must state:
• Soy Candle, Hand Poured, Made in Melbourne,
• A space for the fragrance, size and burn time.
• For this project use Lime, Coconut & Elderfllower, 300grams, 50 Hour burn Time

```html
<!DOCTYPE html>
<html lang="en">
<head>
<meta charset="utf-8">
<title>Clover &amp; Jude — Soy Candle Box with Belly Band</title>
<link rel="stylesheet" href="https://fonts.googleapis.com/css2?family=Varela+Round&family=Cormorant+Garamond:wght@500;600&display=swap">
<style>
  :root {
    --page: #ffffff;
    --box-violet: #6a2d93;
    --box-violet-deep: #561f7e;
    --pattern-tint: #7d3aa6;
    --motif-shade: #5a1f6e;
    --band-plum: #5e1a4b;
    --frame-line: #f1e6f5;
    --ink-light: #f2eef4;
    --ink-soft: #e3d6e3;
    --rule: #b88fb0;
    --fold: rgba(40, 0, 40, 0.35);
  }
  * { margin: 0; padding: 0; box-sizing: border-box; }
  html, body {
    width: 1200px;
    height: 1043px;
    overflow: hidden;
    background: var(--page);
  }
  .canvas { position: relative; width: 1200px; height: 1043px; }

  .panel {
    position: absolute;
    width: 440px;
    height: 440px;
    overflow: hidden;
    outline: 1px solid var(--fold);
  }
  .panel-top   { left: 600px; top: 60px; }
  .panel-side  { left: 160px; top: 500px; }
  .panel-front { left: 600px; top: 500px; }

  .damask-pattern {
    position: absolute;
    inset: 0;
    background: radial-gradient(circle at 50% 45%, var(--pattern-tint) 0%, var(--box-violet) 50%, var(--box-violet-deep) 100%);
  }
  .side-motif {
    position: absolute;
    left: 60px; top: 50px; right: 60px; bottom: 50px;
    border-radius: 45%;
    background: radial-gradient(ellipse at center, var(--motif-shade) 0%, rgba(90, 31, 110, 0.55) 55%, rgba(90, 31, 110, 0) 75%);
  }
  .inset-frame {
    position: absolute;
    inset: 20px;
    border: 1.5px solid var(--frame-line);
    opacity: 0.85;
  }

  .belly-band {
    position: absolute;
    left: 125px;
    width: 190px;
    background: var(--band-plum);
    box-shadow: 0 0 14px rgba(40, 0, 30, 0.35);
    display: flex;
    flex-direction: column;
    align-items: center;
    color: var(--ink-light);
    text-align: center;
  }
  .panel-top .belly-band { top: 0; bottom: 0; justify-content: center; }
  .panel-front .belly-band { top: 0; bottom: 0; }

  .brand-mark {
    display: flex;
    flex-direction: column;
    align-items: center;
    gap: 12px;
  }
  .brand-dot {
    width: 18px; height: 18px;
    border-radius: 50%;
    background: var(--ink-light);
  }
  .brand-name {
    font-family: "Varela Round", sans-serif;
    font-size: 24px;
    color: var(--ink-light);
    white-space: nowrap;
  }
  .panel-top .brand-name { font-size: 18px; }
  .panel-top .brand-dot { width: 12px; height: 12px; }
  .panel-front .brand-mark { margin-top: 70px; }

  .serif {
    font-family: "Cormorant Garamond", serif;
    font-weight: 600;
    color: var(--ink-soft);
  }
  .product-type { margin-top: 40px; font-size: 27px; letter-spacing: 0.5px; }
  .product-method {
    margin-top: 2px;
    padding: 2px 12px;
    border-top: 1px solid var(--rule);
    border-bottom: 1px solid var(--rule);
    font-size: 17px;
  }
  .product-details {
    margin-top: 24px;
    list-style: none;
    font-size: 12px;
    line-height: 1.55;
    letter-spacing: 0.4px;
  }
  .fragrance { font-size: 13px; }
  .origin { margin-top: 20px; font-size: 11px; letter-spacing: 0.6px; }
</style>
</head>
<body>
  <main class="canvas">
    <section class="panel panel-top" aria-label="Box lid">
      <div class="damask-pattern" role="img" aria-label="Violet damask pattern of swirling scrolls and rosettes"></div>
      <div class="belly-band">
        <div class="brand-mark">
          <span class="brand-dot"></span>
          <span class="brand-name">Clover &amp; Jude</span>
        </div>
      </div>
    </section>

    <section class="panel panel-side" aria-label="Box side">
      <div class="damask-pattern" role="img" aria-label="Violet damask pattern of swirling scrolls and rosettes"></div>
      <div class="side-motif" role="img" aria-label="Large faint deep-plum brand motif across the side panel"></div>
    </section>

    <section class="panel panel-front" aria-label="Box front">
      <div class="damask-pattern" role="img" aria-label="Violet damask pattern of swirling scrolls and rosettes"></div>
      <div class="inset-frame"></div>
      <div class="belly-band">
        <div class="brand-mark">
          <span class="brand-dot"></span>
          <span class="brand-name">Clover &amp; Jude</span>
        </div>
        <p class="serif product-type">SOY CANDLE</p>
        <p class="serif product-method">HAND POURED</p>
        <ul class="serif product-details">
          <li class="fragrance">Lime, Coconut &amp; Elderflower</li>
          <li>300 grams</li>
          <li>50 Hour Burn Time</li>
        </ul>
        <p class="serif origin">MADE IN MELBOURNE</p>
      </div>
    </section>
  </main>
</body>
</html>
```